Brightwave Reach - Business Card

We need a business card for a Social Media Marketing company that specializes in online marketing for small businesses in Canada using common Social Media platforms such as Pixlora, Chatterly, Blinkpost & Quibber.

I have uploaded a copy of our logo which I would like utilized in the business card. We would like the business card to be modern yet classy design.

Our website is www.brightwavereach.ca

Industry/Entity Type

Marketing

Contact Information for Business Card

Email: info@brightwavereach.ca
Website: www.brightwavereach.ca
Telephone: 604-555-0193

Colors

Designer to choose colors to be used in the design.

Requirements
Must have
• Social Media icons on reverse
• Please add some designs with color.

```html
<!DOCTYPE html>
<html lang="en">
<head>
<meta charset="utf-8">
<title>Brightwave Reach – Business Card</title>
<link rel="stylesheet" href="https://fonts.googleapis.com/css2?family=Montserrat:wght@800&family=Arimo:wght@400&display=swap">
<style>
  :root {
    --page-bg: #ece9e4;
    --card-bg: #3d4043;
    --band-grey: #9a9b9d;
    --ink-white: #f4f4f4;
    --accent-red: #e0232b;
  }
  * { margin: 0; padding: 0; box-sizing: border-box; }
  html, body {
    width: 1107px;
    height: 1200px;
    overflow: hidden;
  }
  body {
    position: relative;
    background: var(--page-bg);
    font-family: "Arimo", Arial, sans-serif;
    color: var(--ink-white);
  }
  .card {
    position: absolute;
    background: var(--card-bg);
    box-shadow: 0 3px 8px rgba(0,0,0,0.25);
  }

  /* Front */
  .card--front { left: 145px; top: 79px; width: 816px; height: 482px; }
  .edge-band {
    position: absolute;
    top: 3px;
    bottom: 3px;
    width: 27px;
    background: linear-gradient(90deg, var(--band-grey), #b3b4b6 60%, var(--band-grey));
  }
  .edge-band--left { left: 4px; }
  .edge-band--right { right: 4px; }
  .brand-name {
    position: absolute;
    left: 0; right: 0;
    top: 120px;
    text-align: center;
    font-family: "Montserrat", Arial, sans-serif;
    font-weight: 800;
    font-size: 64px;
    line-height: 1.05;
    letter-spacing: 1px;
    text-transform: uppercase;
    color: var(--ink-white);
  }
  .brand-mark {
    display: block;
    width: 22px;
    height: 22px;
    margin: 20px auto 0;
    background: var(--ink-white);
  }
  .front-url {
    position: absolute;
    left: 0; right: 0;
    top: 406px;
    text-align: center;
    font-family: "Montserrat", Arial, sans-serif;
    font-weight: 800;
    font-size: 25px;
    letter-spacing: 1.5px;
    color: var(--ink-white);
  }

  /* Back */
  .card--back { left: 154px; top: 646px; width: 815px; height: 485px; }
  .back-frame {
    position: absolute;
    left: 32px; top: 32px; right: 32px; bottom: 32px;
    border: 7px double var(--ink-white);
  }
  .social-row {
    position: absolute;
    left: 0; right: 0;
    top: 78px;
    display: flex;
    justify-content: center;
    gap: 22px;
  }
  .social-item {
    display: flex;
    align-items: center;
    gap: 7px;
    font-size: 18px;
  }
  .social-dot {
    width: 36px; height: 36px;
    border-radius: 50%;
    background: var(--accent-red);
  }
  .contact-list {
    position: absolute;
    left: 0; right: 0;
    top: 152px;
    list-style: none;
    text-align: center;
  }
  .contact-item { height: 70px; }
  .contact-icon {
    display: block;
    width: 28px; height: 28px;
    margin: 0 auto 4px;
  }
  .contact-text { font-size: 23px; line-height: 28px; }
  .back-signature {
    position: absolute;
    left: 50%;
    bottom: 30px;
    transform: translateX(-50%);
    padding: 0 10px;
    background: var(--card-bg);
    font-family: "Montserrat", Arial, sans-serif;
    font-weight: 800;
    font-size: 22px;
    letter-spacing: 1px;
    text-transform: uppercase;
    white-space: nowrap;
  }
</style>
</head>
<body>

<section class="card card--front" aria-label="Card front">
  <div class="edge-band edge-band--left" role="img" aria-label="Distressed grey texture band"></div>
  <div class="edge-band edge-band--right" role="img" aria-label="Distressed grey texture band"></div>
  <h1 class="brand-name">Brightwave<br>Reach<span class="brand-mark"></span></h1>
  <p class="front-url">WWW.BRIGHTWAVEREACH.CA</p>
</section>

<section class="card card--back" aria-label="Card back">
  <div class="back-frame"></div>

  <ul class="social-row">
    <li class="social-item"><span class="social-dot"></span>Chatterly</li>
    <li class="social-item"><span class="social-dot"></span>Quibber</li>
    <li class="social-item"><span class="social-dot"></span>Pixlora</li>
    <li class="social-item"><span class="social-dot"></span>Blinkpost</li>
  </ul>

  <ul class="contact-list">
    <li class="contact-item">
      <svg class="contact-icon" viewBox="0 0 28 28" aria-hidden="true">
        <circle cx="14" cy="14" r="14" fill="#e0232b"/>
        <rect x="7" y="9" width="14" height="10" fill="none" stroke="#fff" stroke-width="1.6"/>
        <polyline points="7,9 14,15 21,9" fill="none" stroke="#fff" stroke-width="1.6"/>
      </svg>
      <span class="contact-text">info@brightwavereach.ca</span>
    </li>
    <li class="contact-item">
      <svg class="contact-icon" viewBox="0 0 28 28" aria-hidden="true">
        <circle cx="14" cy="14" r="14" fill="#e0232b"/>
        <path d="M10 7 L13 7 L14 11 L12 12.5 Q13.5 16 16 17 L17.5 15 L21 16 L21 19 Q19 21 16 20 Q9.5 17 8 11 Q8 8.5 10 7 Z" fill="#fff"/>
      </svg>
      <span class="contact-text">604-555-0193</span>
    </li>
    <li class="contact-item">
      <svg class="contact-icon" viewBox="0 0 28 28" aria-hidden="true">
        <circle cx="14" cy="14" r="14" fill="#e0232b"/>
        <circle cx="14" cy="14" r="8" fill="none" stroke="#fff" stroke-width="1.5"/>
        <ellipse cx="14" cy="14" rx="3.5" ry="8" fill="none" stroke="#fff" stroke-width="1.3"/>
        <line x1="6" y1="14" x2="22" y2="14" stroke="#fff" stroke-width="1.3"/>
        <line x1="14" y1="6" x2="14" y2="22" stroke="#fff" stroke-width="1.3"/>
      </svg>
      <span class="contact-text">www.brightwavereach.ca</span>
    </li>
  </ul>

  <p class="back-signature">Brightwave Reach</p>
</section>

</body>
</html>
```